Awesome photographers card for an awesome new business

Double sided business card Black background and silver logo in middle on one side. Details on otherside. please keep it simple

Industry/Entity Type

Photographer

Contact Information for Business Card

Gerald Fenwick
0452817360
GeraldFenwickPhotography47@mailbox.test
www.GeraldFenwickPhotography.test.au
Instagram _Gerald_fenwick

Requirements
Must have
• My logo in Silver
• please use instagram logo instead of "Instagram"

```html
<!DOCTYPE html>
<html lang="en">
<head>
<meta charset="UTF-8">
<title>Gerald Fenwick Photography – Business Card</title>
<link rel="stylesheet" href="https://fonts.googleapis.com/css2?family=Bebas+Neue&family=Open+Sans:wght@400;600&display=swap">
<style>
  :root {
    --backdrop: #d6d3cf;
    --card: #050505;
    --silver: #c9c9c9;
    --silver-soft: #a9a9a9;
    --text-light: #e4e4e4;
    --divider: #8a8a8a;
  }
  * { box-sizing: border-box; margin: 0; padding: 0; }
  html, body {
    width: 1200px;
    height: 1000px;
    overflow: hidden;
    background: var(--backdrop);
  }
  .canvas {
    position: relative;
    width: 1200px;
    height: 1000px;
  }
  .card {
    position: absolute;
    left: 266px;
    width: 666px;
    height: 397px;
    background: var(--card);
  }
  .card--front { top: 74px; }
  .card--back { top: 533px; }

  /* Front: brand mark */
  .brand {
    position: absolute;
    left: 213px;
    top: 81px;
    width: 240px;
    height: 240px;
  }
  .brand__ring {
    position: absolute;
    inset: 0;
    border: 4px solid var(--silver);
    border-radius: 50%;
  }
  .brand__name {
    position: absolute;
    inset: 0;
    display: flex;
    flex-direction: column;
    align-items: center;
    justify-content: center;
    font-family: 'Open Sans', sans-serif;
    font-weight: 600;
    color: var(--silver);
    text-align: center;
    letter-spacing: 4px;
    font-size: 17px;
    line-height: 1.6;
  }

  /* Back: identity + contacts */
  .identity {
    position: absolute;
    right: calc(666px - 237px);
    top: 168px;
    text-align: right;
  }
  .identity__name {
    font-family: 'Bebas Neue', sans-serif;
    font-size: 29px;
    letter-spacing: 0.5px;
    color: var(--silver);
    line-height: 1;
  }
  .identity__role {
    font-family: 'Open Sans', sans-serif;
    font-size: 14px;
    color: var(--silver-soft);
    margin-top: 4px;
  }
  .divider {
    position: absolute;
    left: 256px;
    top: 155px;
    width: 1px;
    height: 81px;
    background: var(--divider);
  }
  .contacts {
    position: absolute;
    left: 276px;
    top: 152px;
    list-style: none;
    font-family: 'Open Sans', sans-serif;
    font-size: 14px;
    color: var(--text-light);
  }
  .contacts__item {
    display: flex;
    align-items: center;
    height: 21.5px;
  }
  .contacts__icon {
    width: 12px;
    height: 12px;
    margin-right: 8px;
    flex: none;
  }
</style>
</head>
<body>
<main class="canvas">
  <section class="card card--front" aria-label="Business card front">
    <div class="brand">
      <div class="brand__ring"></div>
      <div class="brand__name">
        <span>GERALD</span>
        <span>FENWICK</span>
        <span>PHOTOGRAPHY</span>
      </div>
    </div>
  </section>

  <section class="card card--back" aria-label="Business card back">
    <div class="identity">
      <div class="identity__name">GERALD FENWICK</div>
      <div class="identity__role">Photographer</div>
    </div>
    <div class="divider"></div>
    <ul class="contacts">
      <li class="contacts__item">
        <svg class="contacts__icon" viewBox="0 0 24 24" aria-hidden="true"><path fill="#bdbdbd" d="M6.6 10.8a15.1 15.1 0 0 0 6.6 6.6l2.2-2.2c.3-.3.7-.4 1-.2 1.1.4 2.3.6 3.6.6.6 0 1 .4 1 1V20c0 .6-.4 1-1 1A17 17 0 0 1 3 4c0-.6.4-1 1-1h3.5c.6 0 1 .4 1 1 0 1.3.2 2.5.6 3.6.1.3 0 .7-.2 1z"/></svg>
        <span>0452817360</span>
      </li>
      <li class="contacts__item">
        <svg class="contacts__icon" viewBox="0 0 24 24" aria-hidden="true"><rect x="3" y="3" width="18" height="18" fill="#bdbdbd"/></svg>
        <span>Gerald_fenwick</span>
      </li>
      <li class="contacts__item">
        <svg class="contacts__icon" viewBox="0 0 24 24" aria-hidden="true"><path fill="#bdbdbd" d="M2 5h20v14H2z"/><path fill="none" stroke="#050505" stroke-width="2" d="M2 6l10 7 10-7"/></svg>
        <span>GeraldFenwickPhotography47@mailbox.test</span>
      </li>
      <li class="contacts__item">
        <svg class="contacts__icon" viewBox="0 0 24 24" aria-hidden="true"><circle cx="12" cy="12" r="9" fill="none" stroke="#bdbdbd" stroke-width="2.5"/><path fill="none" stroke="#bdbdbd" stroke-width="2" d="M3 12h18M12 3c3 3 3 15 0 18M12 3c-3 3-3 15 0 18"/></svg>
        <span>www.GeraldFenwickPhotography.test.au</span>
      </li>
    </ul>
  </section>
</main>
</body>
</html>
```